Tamsorellium we are a young innovative brand about making life easier for people with a disability

Our tag line is Making Life Easy, we are still a relatively new company trying to bring innovation and excitement into the disability space - with latest products and technology - we do have existing website but need to unpgrade for a stronger visual presence.

```html
<!DOCTYPE html>
<html lang="en">
<head>
<meta charset="utf-8">
<title>Tamsorellium — Making Life Easy</title>
<link href="https://fonts.googleapis.com/css2?family=Poppins:wght@400;500;600;700&display=swap" rel="stylesheet">
<style>
:root{
  --red:#e10613;
  --red-dark:#b0000b;
  --black:#111111;
  --ink:#222222;
  --grey:#6b6b6b;
  --light:#f2f2f2;
  --white:#ffffff;
}
*{box-sizing:border-box;margin:0;padding:0}
html,body{width:1200px;height:3880px;overflow:hidden;background:var(--white);font-family:"Poppins",sans-serif;color:var(--ink)}
.page{position:relative;width:1200px;height:3880px}
.abs{position:absolute}

/* top bar */
.topbar{left:0;top:0;width:1200px;height:26px;background:var(--black);color:#ddd;font-size:11px;display:flex;align-items:center;justify-content:space-between;padding:0 120px}
.topbar span{margin-right:16px}
.topbar .right span{margin-left:16px;margin-right:0}
.topbar .dot{display:inline-block;width:7px;height:7px;background:var(--red);border-radius:50%;margin-right:5px}

/* header */
.brand{display:flex;align-items:center;gap:10px;font-weight:700;color:var(--red);font-size:26px;letter-spacing:.5px}
.brand .mark{width:30px;height:30px;border-radius:50%;background:var(--red)}
.header-brand{left:120px;top:62px}
.search{left:770px;top:72px;width:306px;height:32px;display:flex}
.search .field{flex:1;border:1px solid #ccc;font-size:11px;color:#999;padding:8px 10px}
.search .btn{width:34px;background:var(--red);display:flex;align-items:center;justify-content:center}

/* nav */
.nav{left:0;top:146px;width:1200px;height:52px;background:var(--black);display:flex;align-items:center;justify-content:space-between;padding:0 120px;font-size:11px;font-weight:500;color:#fff;letter-spacing:.5px}
.nav .active{color:var(--red)}

/* hero */
.photo{display:block}
.hero-main{left:120px;top:232px;width:552px;height:470px;background:linear-gradient(135deg,#d9cfc4,#9a8f84 60%,#5c5552)}
.hero-top{left:690px;top:232px;width:390px;height:290px;background:linear-gradient(135deg,#f1f1f1,#b8bcc3)}
.hero-bottom{left:690px;top:540px;width:390px;height:362px;background:linear-gradient(135deg,#6a6a6a,#2a2a2a)}
.hero-title{left:120px;top:950px;font-size:40px;font-weight:700;color:var(--black)}
.hero-text{left:120px;top:1018px;width:400px;font-size:12px;line-height:1.6;color:var(--grey)}

/* slider */
.slide{left:185px;top:1100px;width:830px;height:262px;border:3px solid var(--red);background:var(--white)}
.slide-img{left:20px;top:40px;width:180px;height:160px;background:linear-gradient(135deg,#e5e5e5,#8d8d8d)}
.slide-name{left:330px;top:16px;font-size:44px;font-weight:600;letter-spacing:6px;color:var(--black)}
.slide-lead{left:330px;top:82px;font-size:16px;color:var(--ink)}
.slide-list{left:370px;top:110px;font-size:16px;line-height:1.55;color:var(--ink);list-style:none}
.slide-badge{right:18px;bottom:18px;width:120px;height:64px;background:var(--red)}
.dots{left:0;top:1404px;width:1200px;display:flex;justify-content:center;gap:14px}
.dots i{width:9px;height:9px;border-radius:50%;background:#ccc}
.dots i.on{background:var(--red)}

/* categories */
.cats{left:0;top:1510px;width:1200px;height:440px}
.cat{position:absolute;top:0;height:440px;overflow:hidden}
.cat .fill{position:absolute;inset:0}
.cat .label{position:absolute;left:0;right:0;bottom:78px;text-align:center;color:#fff;font-size:22px;font-weight:600}
.cat .link{position:absolute;left:0;right:0;bottom:54px;text-align:center;color:#fff;font-size:12px;font-weight:600}

/* products */
.section-title{left:0;width:1200px;text-align:center;font-size:34px;font-weight:700;color:var(--black)}
.btn-red{background:var(--red);color:#fff;font-size:11px;font-weight:600;letter-spacing:.5px;display:flex;align-items:center;justify-content:center}
.card{width:170px}
.card .img{width:170px;height:236px;background:var(--white);box-shadow:0 4px 18px rgba(0,0,0,.12);display:flex;align-items:center;justify-content:center}
.card .img div{width:110px;height:140px}
.card .name{margin-top:40px;text-align:center;font-size:13px;line-height:1.35;color:var(--ink);height:56px}
.card .price{margin-top:10px;text-align:center;font-size:22px;font-weight:600;color:var(--red)}
.card .price s{font-size:13px;color:var(--grey);font-weight:400;margin-left:4px}

/* sale */
.sale{left:0;top:2700px;width:1200px;height:728px;background:var(--red)}
.sale-title{left:120px;top:2788px;font-size:32px;font-weight:700;color:#fff}
.sale-text{left:120px;top:2852px;width:440px;font-size:12px;line-height:1.7;color:#fff}
.sale-text p{margin-bottom:16px}
.sale-photo{left:600px;top:2700px;width:560px;height:728px;background:linear-gradient(135deg,#c9d3a4,#8ea06a 50%,#5e6f44)}
.sale-tag{left:1160px;top:2700px;width:40px;height:728px;display:flex;align-items:center;justify-content:center}
.sale-tag span{writing-mode:vertical-rl;color:#fff;font-weight:700;font-size:20px;letter-spacing:8px}

/* footer */
.footer{left:0;top:3428px;width:1200px;height:452px;background:var(--black)}
.foot-brand{left:120px;top:3528px;color:var(--white)}
.foot-copy{left:120px;top:3596px;font-size:11px;color:#bbb}
.social{left:120px;top:3654px;display:flex;align-items:center;gap:26px;font-size:16px;font-weight:600;color:var(--white)}
.social .circle{width:30px;height:30px;border-radius:50%;background:var(--red)}
.foot-links{left:120px;top:3718px;font-size:11px;color:#bbb}
.foot-head{font-size:18px;font-weight:600;letter-spacing:.5px;color:var(--white)}
.useful{left:554px;top:3536px}
.useful ul{list-style:none;margin-top:16px;font-size:11px;line-height:1.95;color:#ccc}
.contact{left:828px;top:3536px}
.contact .row{display:flex;align-items:center;gap:16px;margin-top:22px;font-size:11px;color:#ccc}
.contact .ico{width:34px;height:34px;border-radius:50%;border:1px solid #555;display:flex;align-items:center;justify-content:center}
</style>
</head>
<body>
<div class="page">

  <div class="abs topbar">
    <div><span>Healthcare Providers</span><span>|</span><span>CareFund</span><span>|</span><span>About Us</span><span>|</span><span>Contact Us</span></div>
    <div class="right"><span><i class="dot"></i>Cart</span><span><i class="dot"></i>Login or create your account</span></div>
  </div>

  <div class="abs brand header-brand"><span class="mark"></span>Tamsorellium</div>
  <div class="abs search">
    <div class="field">Search products</div>
    <div class="btn">
      <svg width="14" height="14" viewBox="0 0 14 14"><circle cx="6" cy="6" r="4.5" fill="none" stroke="#fff" stroke-width="1.6"/><line x1="9.4" y1="9.4" x2="13" y2="13" stroke="#fff" stroke-width="1.6"/></svg>
    </div>
  </div>

  <nav class="abs nav">
    <span class="active">HOME</span><span>WHEELCHAIRS</span><span>PARTS</span><span>ACCESSORIES</span><span>BARGAIN CENTER</span><span>ONLINE QUOTES</span><span>SCOOTER</span>
  </nav>

  <div class="abs photo hero-main" role="img" aria-label="Photo of a couple at home, one seated in a wheelchair"></div>
  <div class="abs photo hero-top" role="img" aria-label="Photo of a woman in a wheelchair listening to music"></div>
  <div class="abs photo hero-bottom" role="img" aria-label="Photo of a backpack hung on the back of a wheelchair"></div>
  <h1 class="abs hero-title">Making Life Easy</h1>
  <p class="abs hero-text">At Tamsorellium we are all about Making Life Easy. Tamsorellium is an online business focusing on providing choice.</p>

  <div class="abs slide">
    <div class="abs slide-img" role="img" aria-label="Photo of a power assist unit attached to a wheelchair"></div>
    <div class="abs slide-name">SKYLARK</div>
    <div class="abs slide-lead">The new Skylark 2.5 ready to go with new upgrades for 2020</div>
    <ul class="abs slide-list">
      <li>- Dual Disk Brake</li>
      <li>- Full Colour Display</li>
      <li>- USB Phone Charger</li>
      <li>- Improved Quick Release</li>
    </ul>
    <div class="abs slide-badge" role="img" aria-label="Quellan Drive partner badge"></div>
  </div>
  <div class="abs dots"><i class="on"></i><i></i><i></i><i></i><i></i><i></i></div>

  <div class="abs cats">
    <div class="cat" style="left:0;width:196px">
      <div class="fill" role="img" aria-label="Photo of a wheelchair wheel" style="background:linear-gradient(180deg,#f3f3f3 0%,#c8c8c8 55%,var(--red) 100%)"></div>
    </div>
    <div class="cat" style="left:200px;width:410px">
      <div class="fill" role="img" aria-label="Photo of a power assist unit" style="background:linear-gradient(180deg,#ececec 0%,#9a9a9a 45%,var(--red) 80%,var(--red-dark) 100%)"></div>
      <div class="label">Power Assist Units</div><div class="link">Shop Now</div>
    </div>
    <div class="cat" style="left:614px;width:396px">
      <div class="fill" role="img" aria-label="Photo of a wheelchair bag" style="background:linear-gradient(180deg,#3a3a3a 0%,#555 45%,var(--red) 80%,var(--red-dark) 100%)"></div>
      <div class="label">Bags</div><div class="link">Shop Now</div>
    </div>
    <div class="cat" style="left:1014px;width:186px">
      <div class="fill" role="img" aria-label="Photo of wheelchair brakes" style="background:linear-gradient(180deg,#e8e8e8 0%,#8a8a8a 50%,#444 100%)"></div>
      <div class="label" style="text-align:left;left:26px;white-space:nowrap">Brakes/Locks</div>
    </div>
  </div>

  <h2 class="abs section-title" style="top:2040px">Our Products</h2>
  <div class="abs btn-red" style="left:544px;top:2110px;width:112px;height:30px">VIEW ALL</div>

  <div class="abs card" style="left:125px;top:2190px">
    <div class="img"><div role="img" aria-label="Photo of a grey wheelchair pack" style="background:linear-gradient(135deg,#6d6d6d,#2e2e2e)"></div></div>
    <div class="name">Vardo - WHEELCHAIR/ SCOOTER DELUX PAC</div>
    <div class="price">$145</div>
  </div>
  <div class="abs card" style="left:340px;top:2190px">
    <div class="img"><div role="img" aria-label="Photo of a sports wheelchair pack" style="background:linear-gradient(135deg,#5a5a5a,#1f1f1f)"></div></div>
    <div class="name">Vardo - WHEELCHAIR/ SCOOTER SPORTS PAC</div>
    <div class="price">$395</div>
  </div>
  <div class="abs card" style="left:560px;top:2190px">
    <div class="img"><div role="img" aria-label="Photo of a compact power unit with adaptor" style="background:linear-gradient(135deg,#8a8a8a,#3a3a3a 60%,#a33)"></div></div>
    <div class="name">Ember Pact - Compact - with adaptor</div>
    <div class="price">$750<s>$1000</s></div>
  </div>
  <div class="abs card" style="left:790px;top:2190px">
    <div class="img"><div role="img" aria-label="Photo of a twin set power unit" style="background:linear-gradient(135deg,#444,#111 60%,#b22)"></div></div>
    <div class="name">Ember Pact - Twin Set</div>
    <div class="price">$880<s>$1000</s></div>
  </div>

  <div class="abs sale"></div>
  <h2 class="abs sale-title">Wheelchairs For Sale</h2>
  <div class="abs sale-text">
    <p>Are you trying to find the ideal wheelchair? Due to the vast number of possibilities, selecting a simple mobility item like a wheelchair can easily become overwhelming.</p>
    <p>Tamsorellium offers wheelchairs for sale in various sizes, styles, price ranges, and combinations that meet a range of demands and requirements you have.</p>
    <p>Everyone may find wheelchairs at Tamsorellium. We offer manual, power-assist units, and wheelchair accessories for sale any time.</p>
    <p>Speak with a member of our helpful staff about any of our wheelchairs whether a fit finding, or fixed frame or for sport, daily use or for a relaxed family member. Browse and discover a couple of the well-known wheelchair ranges we stock today. Choose from one of the categories above to view our wide selection of high quality wheelchairs and accessories.</p>
    <p>Call or email us to find out more about selecting the ideal wheelchairs for you.</p>
  </div>
  <div class="abs sale-photo" role="img" aria-label="Photo of a smiling woman in a wheelchair outdoors in a garden"></div>
  <div class="abs sale-tag"><span>SALE</span></div>

  <footer class="abs footer"></footer>
  <div class="abs brand foot-brand"><span class="mark"></span>Tamsorellium</div>
  <div class="abs foot-copy">© Copyright 2024 Tamsorellium</div>
  <div class="abs social"><span class="circle"></span><span>PayNest</span><span>Cardora</span></div>
  <div class="abs foot-links">Privacy policy &nbsp;|&nbsp; Contact Us &nbsp;|&nbsp; Shipping details</div>

  <div class="abs useful">
    <div class="foot-head">USEFUL LINKS</div>
    <ul><li>Wheelchairs</li><li>Parts</li><li>Accessories</li><li>Bargain Center</li><li>Online Quotes</li><li>Scooters</li><li>Quotes</li></ul>
  </div>

  <div class="abs contact">
    <div class="foot-head">CONTACT</div>
    <div class="row"><span class="ico"><svg width="14" height="14" viewBox="0 0 24 24"><path d="M6.6 10.8a15 15 0 0 0 6.6 6.6l2.2-2.2c.3-.3.7-.4 1-.2 1.1.4 2.3.6 3.6.6.6 0 1 .4 1 1V20c0 .6-.4 1-1 1A17 17 0 0 1 3 4c0-.6.4-1 1-1h3.5c.6 0 1 .4 1 1 0 1.3.2 2.5.6 3.6.1.3 0 .7-.2 1z" fill="#fff"/></svg></span>1300 482 916</div>
    <div class="row"><span class="ico"><svg width="14" height="14" viewBox="0 0 24 24"><rect x="3" y="5" width="18" height="14" rx="1" fill="none" stroke="#fff" stroke-width="2"/><path d="M3 6l9 7 9-7" fill="none" stroke="#fff" stroke-width="2"/></svg></span>hello@tamsorellium.example</div>
    <div class="row"><span class="ico"><svg width="14" height="14" viewBox="0 0 24 24"><path d="M12 2a7 7 0 0 0-7 7c0 5 7 13 7 13s7-8 7-13a7 7 0 0 0-7-7z" fill="#fff"/><circle cx="12" cy="9" r="2.5" fill="#111"/></svg></span>Harbourton, Australia</div>
  </div>

</div>
</body>
</html>
```